Book Title: “Faith: Road of Endless Grace” Please see the attachment “Text on the cover”.

Book Cover Design Instructions: This book is meant for people of all religions and nationalities. Therefore, on the cover, there should be no mosque or an object specific to any religion. The primary emphasis should be on the "unconditional love of God." Therefore, use universal symbols of love. The second priority themes could be Sufism, Peace, and self-improvement. Rest is your imagination. Please also see the attachment: 'Book description and author's Bio.'
This book has the potential to be a best seller. Please do a good job.
What Book Cover Formats are required: A designer should submit cover designs in three formats: (1) eBook, (2) Paperback, and (3) Hardback. These books will be published on Borvex QPL.
Format requirements for eBooks are available from: https://qpl.borvex.example/en_US/help/topic/R731928457.
You can find paperback and hardback cover measurements from: https://qpl.borvex.example/en_US/cover-calculator
• To complete the project, all three formats should be accepted by Borvex QPL.
• The book interior trim size is 6.14 X 9.21 inches.
• Interior Type: Premium color.
• No bleed.
• I do not upload barcode. So, the back cover should have room for Borvex to print the barcode.
• Number of pages 126.
Compensation for the designer: After selecting one designer, I will increase the amount by $200 on Artvelle to compensate for three deliverables.
Follow-up of the Project:
After the book is published, I may need minor revisions. For example, the number of pages may change. Therefore, I will need the same design in revised sizes. In that case, I will pay $25 for each revision. For example, if the number of pages changes, I will need a different spine for paperback and hardback, then I will pay the artist $25 + $25 = $50 for both designs.
List of Enclosers:
1. Text on the cover.
2. Book description and author's Bio for the back cover.
3. Later, I will upload my picture for the book's back cover.

Target Market(s)

Any adult

Industry/Entity Type

Any industry

Requirements
Must have
• Three Deliverables

```html
<!DOCTYPE html>
<html lang="en">
<head>
<meta charset="utf-8">
<title>Faith: Road of Endless Grace — Full Wrap Cover</title>
<link rel="stylesheet" href="https://fonts.googleapis.com/css2?family=Playfair+Display:ital,wght@0,400;0,500;0,700;1,400&family=Montserrat:wght@600;700&family=Poppins:wght@400;500&display=swap">
<style>
  :root {
    --page-bg: #bdbdbd;
    --sky-top: #9fbccb;
    --sky-mid: #d9dcd6;
    --sky-warm: #f1cfb4;
    --sky-low: #e9b89c;
    --title-orange: #e8611a;
    --title-orange-deep: #c9420c;
    --ink: #141414;
    --ink-soft: #26262a;
    --tree-light: #e9d2b0;
    --tree-mid: #b79a73;
    --tree-dark: #6d5b48;
    --barcode-box: #ffffff;
  }
  * { box-sizing: border-box; margin: 0; padding: 0; }
  html, body { width: 1200px; height: 1200px; overflow: hidden; background: var(--page-bg); }
  .wrap-cover {
    position: absolute; left: 30px; top: 195px;
    width: 1140px; height: 810px;
    display: flex;
    box-shadow: 0 10px 30px rgba(0,0,0,.18);
  }
  .panel {
    position: relative; height: 100%;
    background: linear-gradient(180deg, var(--sky-top) 0%, var(--sky-mid) 40%, var(--sky-warm) 70%, var(--sky-low) 100%);
    overflow: hidden;
  }
  .back-cover { width: 540px; padding: 34px 34px 0 36px; }
  .spine { width: 60px; border-left: 1px solid rgba(255,255,255,.35); border-right: 1px solid rgba(0,0,0,.08); }
  .front-cover { width: 540px; }

  /* back cover */
  .back-title { font-family: "Playfair Display", serif; font-size: 33px; line-height: 1.05; color: var(--ink); }
  .back-title .faith { color: var(--title-orange); font-weight: 700; }
  .back-subtitle { font-family: "Montserrat", sans-serif; font-weight: 700; font-size: 13.5px; color: var(--ink); margin: 6px 0 14px; letter-spacing: -.1px; }
  .blurb p, .bio p { font-family: "Poppins", sans-serif; font-size: 11.4px; line-height: 1.42; color: var(--ink-soft); margin-bottom: 10px; }
  .question-list { font-family: "Playfair Display", serif; font-style: italic; font-size: 12px; line-height: 1.4; color: var(--ink-soft); margin: 0 0 12px 22px; }
  .question-list li { margin-bottom: 6px; padding-left: 4px; }
  em.term { font-family: "Playfair Display", serif; font-style: italic; }
  .author-block { display: flex; gap: 14px; margin-top: 10px; }
  .author-photo { flex: 0 0 92px; height: 118px; border: 1.5px solid var(--ink); }
  .bio-name { font-family: "Playfair Display", serif; font-size: 19px; color: var(--ink); margin-bottom: 4px; }
  .barcode-space { position: absolute; right: 26px; bottom: 24px; width: 178px; height: 112px; background: var(--barcode-box); }

  /* spine */
  .spine-text {
    position: absolute; left: 50%; top: 0;
    transform-origin: 0 0; transform: rotate(90deg) translate(0, -50%);
    width: 810px; height: 60px;
    display: flex; align-items: center; justify-content: space-between;
    padding: 0 40px 0 26px;
    font-family: "Playfair Display", serif; color: var(--ink); white-space: nowrap;
  }
  .spine-title { font-size: 19px; }
  .spine-title .faith { color: var(--title-orange); font-weight: 700; }
  .spine-author { font-size: 19px; font-weight: 500; }

  /* front cover */
  .front-faith {
    position: absolute; top: 40px; left: 0; width: 100%; text-align: center;
    font-family: "Playfair Display", serif; font-weight: 500; font-size: 96px; line-height: 1; letter-spacing: 1px;
    color: var(--title-orange);
    background: linear-gradient(180deg, var(--title-orange) 30%, var(--title-orange-deep) 100%);
    -webkit-background-clip: text; background-clip: text; -webkit-text-fill-color: transparent;
  }
  .front-title {
    position: absolute; top: 140px; left: 0; width: 100%; text-align: center;
    font-family: "Playfair Display", serif; font-weight: 500; font-size: 58px; line-height: 1.02; color: var(--ink);
  }
  .front-subtitle {
    position: absolute; top: 290px; left: 0; width: 100%; text-align: center;
    font-family: "Montserrat", sans-serif; font-weight: 600; font-size: 21px; line-height: 1.3; color: var(--ink);
  }
  .cover-art { position: absolute; left: 0; top: 360px; width: 540px; height: 450px; }
  .front-author {
    position: absolute; bottom: 26px; left: 0; width: 100%; text-align: center;
    font-family: "Playfair Display", serif; font-weight: 500; font-size: 32px; color: var(--ink);
  }
</style>
</head>
<body>
<main class="wrap-cover">
  <section class="panel back-cover">
    <h2 class="back-title"><span class="faith">FAITH:</span>Road of Endless Grace</h2>
    <p class="back-subtitle">GUIDE TO CULTIVATING INNER PEACE AND MINDFUL LIVING</p>
    <div class="blurb">
      <p>This book intricately intertwines the diverse teachings of Sufism with the deep wisdom of the Quran to create a comprehensive roadmap for personal spiritual growth. The reader has a chance to experience firsthand the profound peace and boundless love Sufis have cherished for centuries. This book addresses the following critical questions:</p>
      <ol class="question-list">
        <li>How can one unconditionally love God? It is the greatest of all kinds of love that ignites a profound and transformative spiritual journey.</li>
        <li>How to feel the love of God, which can bring immense peace and contentment.</li>
        <li>How to unconditionally love yourself, which nurtures personal growth and harmony.</li>
        <li>What is the most effective way to respond to life's critical crises to reduce suffering and expedite recovery?</li>
      </ol>
      <p>This book also explores Faith's overwhelming emphasis on avoiding <em class="term">Zulm</em> (oppression and injustice) because the Quran mentions the word <em class="term">Zulm</em> an astounding 291 times. Avoiding <em class="term">Zulm</em> in all human interactions should be the top priority for every Muslim. The Prophet (PBUH) did not just preach peace and love. He gave us a practical example when he took over as a ruler of the Medina without bloodshed. He did not inherit power through the dynasty, and Medina was multi-religious. Arguably, it was history's first large-scale peaceful transfer of power.</p>
      <p>Similarly, he signed the Treaty of Hudaybia with the staunchest enemy, employing an unprecedented peaceful strategy to nonviolently end a bitter war that had claimed hundreds of lives.</p>
      <p>The highlight of this book is that it points to the methodology to acquire a fully satisfied and contented soul (<em class="term">Nafs-e-Mutma'inna</em>) in practical steps, which is the goal of every Sufi wayfarer.</p>
    </div>
    <div class="author-block">
      <div class="author-photo" role="img" aria-label="Space for the author's portrait"></div>
      <div class="bio">
        <h3 class="bio-name">Dr. Noreen Valdane</h3>
        <p>Dr. Valdane holds a Master's in Physics and a Master's in Computer Science and worked as a Software Engineer. He earned his Ph.D. in Islamic Studies. He was one of the founders of a mosque in Virginia.</p>
      </div>
    </div>
    <div class="barcode-space" aria-label="Reserved space for barcode"></div>
  </section>

  <section class="panel spine">
    <div class="spine-text">
      <span class="spine-title"><span class="faith">FAITH:</span>Road of Endless Grace</span>
      <span class="spine-author">Dr. Noreen Valdane</span>
    </div>
  </section>

  <section class="panel front-cover">
    <h1 class="front-faith">FAITH</h1>
    <p class="front-title">Road of Endless<br>Grace</p>
    <p class="front-subtitle">Guide to Cultivating Inner Peace<br>and Mindful Living</p>
    <svg class="cover-art" viewBox="0 0 540 450" role="img" aria-label="Illustration of a large blossoming tree with sprawling roots on a grassy knoll at sunset">
      <defs>
        <radialGradient id="glow" cx="0.72" cy="0.35" r="0.6">
          <stop offset="0" stop-color="#fbd9a4"/>
          <stop offset="1" stop-color="#fbd9a4" stop-opacity="0"/>
        </radialGradient>
        <radialGradient id="canopy" cx="0.6" cy="0.45" r="0.6">
          <stop offset="0" stop-color="var(--tree-light)"/>
          <stop offset="0.7" stop-color="var(--tree-mid)"/>
          <stop offset="1" stop-color="var(--tree-dark)" stop-opacity="0.7"/>
        </radialGradient>
        <linearGradient id="ground" x1="0" y1="0" x2="0" y2="1">
          <stop offset="0" stop-color="#8d8a5c"/>
          <stop offset="1" stop-color="#5f6b4a"/>
        </linearGradient>
      </defs>
      <rect width="540" height="450" fill="url(#glow)"/>
      <ellipse cx="280" cy="150" rx="240" ry="150" fill="url(#canopy)"/>
      <path d="M0 380 Q180 330 330 360 T540 350 L540 450 L0 450 Z" fill="url(#ground)"/>
    </svg>
    <p class="front-author">Dr. Noreen Valdane</p>
  </section>
</main>
</body>
</html>
```